OpenHarbor Yoga Website Design

Business Logo - attached
5 pages being:
Home
About
Classes
Blog
Contact

Would like Scrolling webpage and yoga symbols to be used.

Must have's being:
Easy to navigate, Text needs to be able to be edited/updated, Enquire Now Links, More Information Links, be a secure site, SEO,

Please refer to attached document for the information for the body of the website.

Target Market(s)

Educators, Community Service, Health and Wellbeing, Mental Health

Industry/Entity Type

Yoga

Coding

Coded - Design and coding required

Number of Pages Required

5+ page

Font styles to use
Other font styles liked:
• Bella Bold BC

Colors
0094D4
00A9DD
6FCCEA
C7EBF8
E9F6FB
6B429C
8869AF
B7A5CE
E3DAEB
F3F0F8

Requirements
Must have
• Easy to navigate, Text needs to be able to be edited/updated, Enquire Now Links, More Information Links, be a secure site, SEO,
Nice to have
• Scrolling webpage, yoga symbols

```html
<!DOCTYPE html>
<html lang="en">
<head>
<meta charset="utf-8">
<title>OpenHarbor Yoga</title>
<link rel="stylesheet" href="https://fonts.googleapis.com/css2?family=Caveat+Brush&family=Josefin+Sans:wght@300;400&family=Quicksand:wght@400;500&display=swap">
<style>
:root{
  --purple:#5a10d6;
  --purple-deep:#3e0ba8;
  --purple-soft:#8869af;
  --lilac:#b7a5ce;
  --lilac-pale:#f3f0f8;
  --blue-bar:#1a4dff;
  --ink:#111;
  --text:#333;
  --white:#fff;
  --black:#000;
}
*{margin:0;padding:0;box-sizing:border-box}
html,body{width:1200px;height:2724px;overflow:hidden;background:var(--white)}
body{position:relative;font-family:'Josefin Sans',sans-serif;color:var(--text)}
.brush{font-family:'Caveat Brush',cursive}
.abs{position:absolute}

/* hero */
.hero{position:absolute;left:0;top:0;width:1200px;height:619px;
  background:linear-gradient(180deg,#5b6a7a 0%,#8a8a80 18%,#4d6b8c 40%,#27476e 65%,#6e6f7a 92%,#8a7a70 100%)}
.hero-photo{position:absolute;left:600px;top:130px;width:310px;height:460px;border-radius:140px 140px 20px 20px;
  background:linear-gradient(180deg,#c9b9a8,#e3e1df 45%,#8d9bb3 100%);opacity:.85}
.nav{position:absolute;left:209px;top:57px;width:781px;height:62px;background:var(--white);border-radius:31px}
.nav a{position:absolute;top:18px;font-family:'Caveat Brush',cursive;font-size:24px;color:var(--ink);text-decoration:none;letter-spacing:.5px}
.nav-logo{position:absolute;left:317px;top:-52px;width:154px;height:154px;border-radius:50%;background:var(--white);
  display:flex;align-items:center;justify-content:center;text-align:center;font-family:'Caveat Brush',cursive;font-size:24px;line-height:1.05;color:var(--purple)}
.search{position:absolute;left:938px;top:79px}
.welcome{left:98px;top:182px;font-size:26px;color:var(--white)}
.hero-title{left:98px;top:222px;font-size:80px;line-height:1.1;color:var(--white);letter-spacing:1px}
.hero-text{left:101px;top:337px;width:450px;font-size:16px;line-height:31px;color:var(--white);font-weight:300}
.btn{position:absolute;display:flex;align-items:center;justify-content:center;font-family:'Caveat Brush',cursive;color:var(--white);
  background:linear-gradient(90deg,var(--purple-deep),#7c45f0 60%,#d9c8ff);border-radius:6px;box-shadow:4px 4px 0 var(--white),5px 5px 0 var(--purple)}
.btn-book{left:101px;top:458px;width:168px;height:48px;font-size:26px}

/* about */
.dots{left:232px;top:726px;width:330px;height:420px;
  background-image:radial-gradient(circle,#c8c8c8 1.6px,transparent 1.8px);background-size:16px 16px}
.about-main{left:98px;top:755px;width:362px;height:470px;background:linear-gradient(135deg,#e8e4dc,#7a3a36 55%,#8a2e30)}
.about-inset{left:358px;top:963px;width:182px;height:242px;background:linear-gradient(180deg,#dfe7ef,#6d8aa0 60%,#a9c7e0);box-shadow:0 10px 30px rgba(0,0,0,.25)}
.about-title{left:603px;top:740px;font-size:52px;color:var(--ink)}
.om{width:46px;height:46px;border-radius:50%;border:2px solid var(--purple-soft);background:var(--lilac-pale)}
.about-text{left:603px;top:824px;width:490px;font-size:14px;line-height:23.5px;color:var(--ink);font-weight:300}
.about-text p{margin-bottom:22px}
.about-text p:last-child{margin-bottom:0}
.btn-enquire{left:607px;top:1132px;width:143px;height:43px;font-size:22px}
.glow{left:880px;top:1100px;width:320px;height:400px;border-radius:50%;background:radial-gradient(circle,#efeaf8 0%,rgba(255,255,255,0) 70%)}

/* benefits */
.ben-title{left:0;top:1412px;width:1200px;text-align:center;font-size:56px;color:var(--ink)}
.card{position:absolute;top:1548px;width:319px;height:592px;background:var(--white);box-shadow:0 4px 18px rgba(0,0,0,.08)}
.card-img{height:210px}
.card-bar{height:5px;background:var(--blue-bar)}
.card-head{position:absolute;left:16px;top:245px;display:flex;align-items:center}
.card-icon{width:72px;height:67px;border:3px solid var(--purple);background:var(--lilac-pale)}
.card-head h3{margin-left:18px;font-family:'Caveat Brush',cursive;font-weight:400;font-size:30px;color:var(--ink)}
.card ul{position:absolute;left:16px;top:333px;width:296px;list-style:none;font-family:'Quicksand',sans-serif;font-size:14.5px;line-height:21.5px;color:#333;letter-spacing:.4px}
.card li{position:relative;padding-left:31px}
.card li::before{content:"";position:absolute;left:1px;top:5px;width:11px;height:11px;border-radius:50%;background:var(--purple)}

/* footer */
.footer{position:absolute;left:0;top:2217px;width:1200px;height:507px;background:var(--black);color:var(--white)}
.foot-logo{position:absolute;left:520px;top:40px;width:160px;height:160px;border-radius:50%;border:2px solid var(--purple);
  display:flex;align-items:center;justify-content:center;text-align:center;font-family:'Caveat Brush',cursive;font-size:28px;line-height:1.05;color:var(--lilac)}
.contact{position:absolute;top:145px;display:flex;align-items:center;font-family:'Caveat Brush',cursive;font-size:24px}
.contact .ic{width:48px;height:48px;border-radius:50%;background:var(--purple);display:flex;align-items:center;justify-content:center;margin-right:12px}
.foot-nav{position:absolute;top:258px;left:0;width:1200px;display:flex;justify-content:center;gap:34px;font-family:'Caveat Brush',cursive;font-size:24px}
.social{position:absolute;top:330px;width:38px;height:38px;border-radius:50%;border:2px solid var(--white)}
.rule{position:absolute;left:98px;top:400px;width:1004px;height:1px;background:#888}
.copy{position:absolute;top:432px;left:0;width:1200px;text-align:center;font-family:'Caveat Brush',cursive;font-size:19px}
</style>
</head>
<body>

<section class="hero">
  <div class="hero-photo" role="img" aria-label="Woman meditating cross-legged on a lakeside jetty at dawn"></div>
  <nav class="nav">
    <a style="left:30px">HOME</a>
    <a style="left:115px">ABOUT</a>
    <a style="left:205px">CLASSES</a>
    <div class="nav-logo">OpenHarbor<br>Yoga</div>
    <a style="left:522px">BLOG</a>
    <a style="left:590px">CONTACT</a>
  </nav>
  <svg class="search" width="26" height="26" viewBox="0 0 26 26"><circle cx="10.5" cy="10.5" r="7.5" fill="none" stroke="#5a10d6" stroke-width="3.5"/><line x1="16" y1="16" x2="23" y2="23" stroke="#5a10d6" stroke-width="4" stroke-linecap="round"/></svg>
  <div class="abs welcome brush">Welcome To</div>
  <h1 class="abs hero-title brush" style="font-weight:400">OPENHARBOR YOGA</h1>
  <p class="abs hero-text">OpenHarbor Yoga believe that you are never too young to benefit from and fall in love with yoga. My aim is to EMPOWER kids and teens to thrive by teaching life skills in</p>
  <a class="btn btn-book">Book Now</a>
</section>

<section>
  <div class="abs glow"></div>
  <div class="abs dots"></div>
  <div class="abs about-main" role="img" aria-label="Woman in red activewear meditating with hands in prayer"></div>
  <div class="abs about-inset" role="img" aria-label="Woman in a seated twist yoga pose on a blue mat"></div>
  <h2 class="abs about-title brush" style="font-weight:400;display:flex;align-items:center;gap:18px">ABOUT US <span class="om" role="img" aria-label="Om symbol ornament"></span></h2>
  <div class="abs about-text">
    <p>Hi and welcome to OpenHarbor Yoga!<br>My name is Rosalind, and I am the creator &amp; facilitator of OpenHarbor Yoga.</p>
    <p>With the increasing numbers of youth mental health, I have started OpenHarbor Yoga wanting to assist children and teens with their mental health for life, with the magic of yoga.</p>
    <p>I had always wanted to teach children, but had never found the right platform to do so... That was until I found yoga!</p>
    <p>I genuinely believe the practice of yoga and mindfulness especially at a young age can offer life-long tools to kids and teens such as dealing with</p>
  </div>
  <a class="btn btn-enquire">Enquire Now</a>
</section>

<section>
  <div class="abs om" style="left:576px;top:1358px;width:48px;height:48px" role="img" aria-label="Om symbol ornament"></div>
  <h2 class="abs ben-title brush" style="font-weight:400">BENEFITS OF YOGA</h2>

  <article class="card" style="left:98px">
    <div class="card-img" role="img" aria-label="Woman in a pigeon pose stretch in a bright room" style="background:linear-gradient(180deg,#dcd8d0,#a9a49a 70%,#6b6660)"></div>
    <div class="card-bar"></div>
    <div class="card-head"><div class="card-icon" role="img" aria-label="Stretching pose icon"></div><h3>HEALTHY BODIES</h3></div>
    <ul>
      <li>Develops strong, flexible and healthy bodies</li>
      <li>Promotes spinal alignment and good posture</li>
      <li>Builds energy and stamina</li>
      <li>Improves internal physical function - organs, digestion, elimination, circulation, and blood flow.</li>
      <li>Helps breathing and lung capacity</li>
      <li>Teaches the enjoyment of movement</li>
      <li>Works the 'whole' body</li>
    </ul>
  </article>

  <article class="card" style="left:440px">
    <div class="card-img" role="img" aria-label="Woman meditating in lotus pose in a sunlit room" style="background:linear-gradient(180deg,#efe6d6,#cdb89a 60%,#8f7a62)"></div>
    <div class="card-bar"></div>
    <div class="card-head"><div class="card-icon" role="img" aria-label="Meditation pose icon"></div><h3>HEALTHY MINDS</h3></div>
    <ul>
      <li>Cultivates confidence and self-esteem</li>
      <li>Develops concentration and attention</li>
      <li>Clears the mind for better clarity and decision making</li>
      <li>Helps relax and sleep better</li>
      <li>Calms the nervous system</li>
      <li>Learns to cope with stressful situations</li>
      <li>Balances emotions</li>
    </ul>
  </article>

  <article class="card" style="left:780px">
    <div class="card-img" role="img" aria-label="Two people doing partner acro yoga on a beach" style="background:linear-gradient(180deg,#8e9092,#b7b8b6 45%,#5d666d)"></div>
    <div class="card-bar"></div>
    <div class="card-head"><div class="card-icon" role="img" aria-label="Lotus flower icon"></div><h3>HEALTHY SPIRITS</h3></div>
    <ul>
      <li>Fosters creativity, expression and imagination</li>
      <li>Cultivates kindness to themselves and others</li>
      <li>Cultivates respect for self and others</li>
      <li>Builds balance and inner quiet</li>
      <li>Builds inner strength and resilience</li>
      <li>Teaches self-awareness</li>
      <li>Focuses on positive self-talk</li>
    </ul>
  </article>
</section>

<footer class="footer">
  <div class="foot-logo">OpenHarbor<br>Yoga</div>
  <div class="contact" style="left:242px">
    <span class="ic"><svg width="22" height="22" viewBox="0 0 24 24"><path fill="#fff" d="M6.6 10.8a15 15 0 0 0 6.6 6.6l2.2-2.2a1 1 0 0 1 1-.25 11.4 11.4 0 0 0 3.6.57 1 1 0 0 1 1 1V20a1 1 0 0 1-1 1A17 17 0 0 1 3 4a1 1 0 0 1 1-1h3.5a1 1 0 0 1 1 1c0 1.25.2 2.45.57 3.57a1 1 0 0 1-.25 1z"/></svg></span>
    +1 0400 555 018
  </div>
  <div class="contact" style="left:757px">
    <span class="ic"><svg width="24" height="18" viewBox="0 0 24 18"><rect x="1.5" y="1.5" width="21" height="15" rx="2" fill="none" stroke="#fff" stroke-width="2"/><path d="M2 2l10 8 10-8" fill="none" stroke="#fff" stroke-width="2"/></svg></span>
    HELLO@OPENHARBORYOGA.EXAMPLE
  </div>
  <nav class="foot-nav"><span>HOME</span><span>ABOUT</span><span>CLASSES</span><span>BLOG</span><span>CONTACT</span><span>MORE INFORMATION</span></nav>
  <a class="social" style="left:554px" aria-label="Social profile"></a>
  <a class="social" style="left:608px" aria-label="Social profile"></a>
  <div class="rule"></div>
  <p class="copy">© copyrights 2023 OpenHarbor Yoga All Rights Reserved</p>
</footer>

</body>
</html>
```